Stylish Business Cards Wanted

- DOUBLE SIDED Design Required -

High end, edgy cards for a corporate and personal stylist. Must include logo,
Name: Belinda Harwick
Title: Director and Stylist
telephone : +61 8 7142 5809
email: belinda@theloombriefing.example
website: theloombriefing.example
Tag: Corporate Workwear & Uniform Specialist | Personal Stylist
Would like nice icons for telephone, email, website

Target Market(s)

Businesses wanting stylish uniforms, people wanting stylish wardrobes

Industry/Entity Type

Corporate Workwear Stylist

Contact Information for Business Card

I would like black, white and gold foiling incorporated in the design - possibly a touch of the other colours on my branding guide attached Name: Belinda Harwick Title: Director and Stylist telephone : +61 8 7142 5809 email: belinda@theloombriefing.example website: theloombriefing.example Tag: Corporate Workwear & Uniform Specialist | Personal Stylist Would like nice icons for telephone, email, website

Font styles to use
Other font styles liked:
• Raleway

Colors

Designer to choose colors to be used in the design.

Requirements
Must have
• Gold foil accents

```html
<!DOCTYPE html>
<html lang="en">
<head>
<meta charset="utf-8">
<title>The Loom Briefing — Business Card</title>
<link href="https://fonts.googleapis.com/css2?family=Roboto:wght@400;500&family=Satisfy&family=Dancing+Script:wght@500&display=swap" rel="stylesheet">
<style>
  :root {
    --backdrop: #d8cec3;
    --card: #eef0f1;
    --card-edge: #ffffff;
    --ink: #1f2431;
    --gold: #c9a85a;
    --gold-deep: #b8934a;
  }
  * { margin: 0; padding: 0; box-sizing: border-box; }
  html, body {
    width: 1200px; height: 1054px; overflow: hidden;
    background: var(--backdrop);
  }
  .business-card {
    position: absolute; left: 100px; top: 224px;
    width: 1000px; height: 606px;
    background: linear-gradient(160deg, #f4f5f6 0%, var(--card) 60%, #e6e8ea 100%);
    border: 1px solid var(--card-edge);
    border-radius: 24px;
    box-shadow: 0 18px 40px rgba(60, 45, 30, 0.18);
    color: var(--ink);
    font-family: "Roboto", Arial, sans-serif;
  }
  .holder-name {
    position: absolute; left: 55px; top: 84px;
    font-family: "Dancing Script", cursive;
    font-weight: 500; font-size: 54px; line-height: 1;
    color: var(--gold);
  }
  .holder-title {
    position: absolute; left: 55px; top: 165px;
    font-size: 25px; font-weight: 400; color: var(--ink);
  }
  .brand-name {
    position: absolute; left: 600px; top: 118px; width: 330px;
    display: flex; align-items: center; gap: 16px;
    font-size: 40px; font-weight: 500; line-height: 1.05;
    color: var(--ink);
  }
  .brand-mark {
    flex: none; width: 22px; height: 22px; background: var(--ink);
  }
  .contact-list {
    position: absolute; left: 62px; top: 390px;
    list-style: none;
  }
  .contact-item {
    display: flex; align-items: center; gap: 16px;
    height: 42px; font-size: 25px; color: var(--ink);
  }
  .contact-icon { width: 24px; height: 24px; flex: none; }
  .tagline {
    position: absolute; left: 55px; top: 528px;
    font-family: "Satisfy", cursive; font-size: 31px; color: var(--ink);
    white-space: nowrap;
  }
  .tagline-divider { color: var(--gold); margin: 0 12px; }
</style>
</head>
<body>
  <main class="business-card">
    <h1 class="holder-name">Belinda Harwick</h1>
    <p class="holder-title">Director and Stylist</p>

    <div class="brand-name"><span class="brand-mark"></span><span>The Loom Briefing</span></div>

    <ul class="contact-list">
      <li class="contact-item">
        <svg class="contact-icon" viewBox="0 0 24 24" fill="none" stroke="var(--gold)" stroke-width="1.6">
          <circle cx="12" cy="12" r="10.5"/>
          <path d="M8.3 7.2c.5-.4 1.1-.3 1.4.2l.9 1.6c.2.4.1.9-.2 1.2l-.6.5c.6 1.3 1.5 2.3 2.8 2.9l.5-.6c.3-.3.8-.4 1.2-.2l1.6.9c.5.3.6.9.2 1.4l-.6.7c-.6.6-1.5.8-2.3.4-2.5-1.2-4.4-3.1-5.6-5.6-.4-.8-.2-1.7.4-2.3z" stroke-linejoin="round"/>
        </svg>
        <span>+61 8 7142 5809</span>
      </li>
      <li class="contact-item">
        <svg class="contact-icon" viewBox="0 0 24 24" fill="none" stroke="var(--gold)" stroke-width="1.6">
          <rect x="2" y="5" width="20" height="14" rx="1.5"/>
          <path d="M2.5 6l9.5 7 9.5-7" stroke-linejoin="round"/>
        </svg>
        <span>belinda@theloombriefing.example</span>
      </li>
      <li class="contact-item">
        <svg class="contact-icon" viewBox="0 0 24 24" fill="none" stroke="var(--gold)" stroke-width="1.5">
          <circle cx="12" cy="12" r="10"/>
          <ellipse cx="12" cy="12" rx="4.3" ry="10"/>
          <path d="M2 12h20M3.5 7h17M3.5 17h17"/>
        </svg>
        <span>www.theloombriefing.example</span>
      </li>
    </ul>

    <p class="tagline">Corporate Workwear &amp; Uniform Specialist<span class="tagline-divider">/</span>Personal Stylist</p>
  </main>
</body>
</html>
```